Window company.

Hello,

We are a small family business located in Madrid, Spain that works nationwide to fix, change or mount the windows of your home / premises.

The group of possible clients to whom the flyer is focused ranges from 30 to 65 years, families in general who want comfort at home and extra savings every year in heating.

It must include not only graphics and a striking aesthetic in accordance with the concepts of wanting to reach / transmit the final product to the customer to sell the product.

Details to also include:

-Brief history of the company and its foundation in 2006. It will be subsequently translated into Spanish so put in words what you consider necessary so that the client stays with the concept that we are professionals.

--Specialized in exterior aluminum and PVC carpentry.

-We move to your home for a first visit and we provide the budget totally free without any commitment.

- Also payment facilities; up to 3 times, without interest.

-Contact details of the company. (QuickChat, email, phone and location)
Open: Mon - Friday 11,00am - 9pm
Saturday: 12,00am - 7pm
Sunday: Closed

Also as a suggestion, to decide on your own, graphics of types of window openings, if you consider that anything that is striking for the client so it wonr be yet another advertising flyer.

We are open to all kinds of ideas, all of them involving marketing branding.

We are open to any type of idea and we want to stand out, the construction world is tough and we have an idea to grow, taking into account that it must not only be beautiful but commercial to attract potential customers with all kinds of purchasing power.

Thank you.

```html
<!DOCTYPE html>
<html lang="en">
<head>
<meta charset="utf-8">
<title>Ventalux – Window Flyer</title>
<link href="https://fonts.googleapis.com/css2?family=Poppins:wght@400;500;600&family=Roboto:wght@400;500;700&display=swap" rel="stylesheet">
<style>
  :root{
    --red:#d40f14;
    --ink:#222222;
    --grey-text:#5a5a5a;
    --logo-grey:#6d6d6d;
    --tile:#efeeeb;
    --tile-line:#d9d9d6;
    --chevron:#8a8a8a;
    --stage:#e4e4e4;
    --paper:#ffffff;
    --map-tone:#e7e5e1;
  }
  *{margin:0;padding:0;box-sizing:border-box}
  html,body{width:1200px;height:720px;overflow:hidden;background:var(--stage)}
  .canvas{position:relative;width:1200px;height:720px}
  .flyer{position:absolute;top:54px;width:437px;height:612px;background:var(--paper);overflow:hidden;box-shadow:0 2px 8px rgba(0,0,0,.18)}
  .flyer--front{left:131px}
  .flyer--back{left:647px}
  .deco{position:absolute;inset:0;width:437px;height:612px}
  .brand{position:absolute;left:38px;top:62px;display:flex;align-items:center;gap:10px}
  .brand__mark{width:14px;height:14px;background:var(--red)}
  .brand__name{font-family:'Roboto',sans-serif;font-weight:500;font-size:30px;letter-spacing:1px;color:var(--logo-grey)}
  .headline{position:absolute;left:36px;top:116px;font-family:'Poppins',sans-serif;font-weight:600;font-size:14.2px;line-height:14.5px;color:var(--red);text-transform:uppercase;white-space:nowrap}
  .headline span{font-weight:400}
  .services{position:absolute;left:166px;top:169px;font-family:'Roboto',sans-serif;font-weight:500;font-size:15.8px;line-height:16px;color:var(--ink);white-space:nowrap}
  .free-visit{position:absolute;left:225px;top:246px;width:200px;text-align:center;font-family:'Poppins',sans-serif;font-size:14px;line-height:14px;color:var(--grey-text);white-space:nowrap}
  .free-visit strong{color:var(--red);font-weight:600}
  .speciality{position:absolute;left:110px;top:366px;width:180px;text-align:center;font-family:'Poppins',sans-serif;font-size:13.8px;line-height:14px;color:#fff}
  .payment{position:absolute;left:27px;top:451px;width:150px;font-family:'Poppins',sans-serif;font-size:13.8px;line-height:14px;color:var(--ink)}
  .call{position:absolute;left:141px;top:536px;font-family:'Poppins',sans-serif;font-size:14px;color:var(--red)}
  .call__number{display:block;font-family:'Roboto',sans-serif;font-weight:700;font-size:30px;line-height:34px;margin-top:2px;letter-spacing:.5px}
  .section-title{position:absolute;left:36px;font-family:'Roboto',sans-serif;font-weight:700;font-size:12px;color:var(--red)}
  .about-text{position:absolute;left:36px;top:203px;font-family:'Roboto',sans-serif;font-size:11.6px;line-height:12px;color:var(--grey-text);white-space:nowrap}
  .contact-line{position:absolute;left:36px;display:flex;align-items:center;gap:6px;font-family:'Roboto',sans-serif;color:var(--ink)}
  .contact-line svg{flex:none}
  .contact-line--address{top:287px;font-size:14px}
  .contact-line--phone{top:314px;font-size:17.5px;font-weight:500}
  .hours{position:absolute;left:36px;top:344px;font-family:'Roboto',sans-serif;font-size:12px;line-height:12px;color:var(--ink)}
  .social{position:absolute;left:36px;display:flex;align-items:center;gap:8px;font-family:'Roboto',sans-serif;font-size:10.5px;color:var(--grey-text)}
  .social__dot{width:22px;height:22px;border-radius:50%;background:var(--logo-grey)}
</style>
</head>
<body>
<div class="canvas">

  <section class="flyer flyer--front">
    <svg class="deco" viewBox="0 0 437 612">
      <polyline points="279,0 373,77 437,24" fill="none" stroke="var(--chevron)" stroke-width="3"/>
      <polyline points="318,0 373,44 425,0" fill="none" stroke="var(--tile-line)" stroke-width="1.5"/>
      <polyline points="330,0 373,34 413,0" fill="none" stroke="var(--tile-line)" stroke-width="1.5"/>
      <polygon points="437,320 310,425 437,530" fill="none" stroke="var(--tile-line)" stroke-width="1.5"/>
      <polygon points="342,402 437,482 342,562 247,482" fill="var(--tile)" stroke="var(--tile-line)" stroke-width="1.5"/>
      <polygon points="342,414 424,482 342,550 260,482" fill="none" stroke="var(--tile-line)" stroke-width="1"/>
      <polygon points="437,395 360,462 437,520" fill="var(--tile)"/>
      <polyline points="210,612 437,420" fill="none" stroke="var(--tile-line)" stroke-width="1.5"/>
      <polyline points="330,612 437,525" fill="none" stroke="var(--tile-line)" stroke-width="1.5"/>
      <polygon points="0,346 34,372 0,398" fill="#dcdbd8"/>
      <polyline points="0,322 60,372 0,420" fill="none" stroke="var(--red)" stroke-width="3"/>
      <g role="img" aria-label="Photo: installer sealing a window frame on a ladder">
        <polygon points="67,157 196,266 67,375 -62,266" fill="#8ea3b8"/>
      </g>
      <g role="img" aria-label="Photo in red tone: worker fitting an aluminium frame">
        <polygon points="202,269 331,373 202,480 75,373" fill="var(--red)"/>
        <polygon points="202,269 331,373 202,480 260,373" fill="#a40c10" opacity=".55"/>
      </g>
      <g role="img" aria-label="Faded photo: hands measuring a wooden frame">
        <polygon points="68,378 196,485 68,593 -58,485" fill="#d6c8bf"/>
      </g>
      <polygon points="0,542 63,593 41,612 0,612" fill="var(--red)"/>
    </svg>

    <div class="brand"><span class="brand__mark"></span><span class="brand__name">VENTALUX</span></div>
    <h1 class="headline">Fix, change or mount the windows of your<br>home <span>or premises.</span></h1>
    <p class="services">Carpinteria de exterior - Toldos -<br>Aluminio - Acristalamientos - PVC<br>- Mosquiteras - Lucernarios</p>
    <p class="free-visit">We move to your home for<br>a first visit and we provide<br>the budget <strong>TOTALLY</strong><br><strong>FREE</strong> without any<br>commitment.</p>
    <p class="speciality">Specialized in exterior<br>aluminum and PVC<br>carpentry.</p>
    <p class="payment">Also payment<br>facilities;<br>up to 3 times,<br>without interest.</p>
    <p class="call">Call now!<span class="call__number">+34 600 41 27 95</span></p>
  </section>

  <section class="flyer flyer--back">
    <svg class="deco" viewBox="0 0 437 612">
      <polyline points="279,0 373,77 437,24" fill="none" stroke="var(--chevron)" stroke-width="3"/>
      <polyline points="318,0 373,44 425,0" fill="none" stroke="var(--tile-line)" stroke-width="1.5"/>
      <polyline points="330,0 373,34 413,0" fill="none" stroke="var(--tile-line)" stroke-width="1.5"/>
      <polygon points="437,68 342,148 437,230" fill="var(--tile)"/>
      <polygon points="330,148 430,230 330,312 230,230" fill="var(--tile)" stroke="var(--tile-line)" stroke-width="1.5" opacity=".7"/>
      <polygon points="437,262 345,338 437,410" fill="var(--tile)" opacity=".8"/>
      <polyline points="60,330 437,20" fill="none" stroke="var(--tile-line)" stroke-width="1"/>
      <polygon points="0,342 34,368 0,400" fill="#dcdbd8"/>
      <g role="img" aria-label="Map showing the business location">
        <polygon points="295,329 456,462 295,596 134,462" fill="var(--map-tone)" stroke="var(--tile-line)" stroke-width="2"/>
      </g>
      <polygon points="127,468 222,545 127,612 32,545" fill="#dad9d6"/>
      <polygon points="0,535 66,589 42,612 0,612" fill="var(--red)"/>
    </svg>

    <div class="brand"><span class="brand__mark"></span><span class="brand__name">VENTALUX</span></div>
    <h1 class="headline">Fix, change or mount the windows of your<br>home <span>or premises.</span></h1>

    <h2 class="section-title" style="top:180px">ABOUT US</h2>
    <p class="about-text">History of the company and its foundation in 2006. It will be<br>subsequently translated into Spanish so put in words what you<br>consider necessary so that the client stays with the concept that we<br>are professionals.</p>

    <h2 class="section-title" style="top:267px">WE LOCATE</h2>
    <p class="contact-line contact-line--address">
      <svg width="9" height="13" viewBox="0 0 9 13"><path d="M4.5 0A4.5 4.5 0 0 0 0 4.5C0 8 4.5 13 4.5 13S9 8 9 4.5A4.5 4.5 0 0 0 4.5 0Zm0 6.3a1.8 1.8 0 1 1 0-3.6 1.8 1.8 0 0 1 0 3.6Z" fill="var(--logo-grey)"/></svg>
      Pol. Ind. Las Veredas II
    </p>
    <p class="contact-line contact-line--phone">
      <svg width="11" height="13" viewBox="0 0 11 13"><path d="M2.5 1 4.3 3.4 3.2 4.8C3.8 6.6 5 8 6.5 9l1.3-1 2.3 1.8-1.4 2C5 11.4 1.5 7.3 1 2.4Z" fill="none" stroke="var(--logo-grey)" stroke-width="1.1" stroke-linejoin="round"/></svg>
      +34 600 41 27 95
    </p>
    <p class="hours">Open: Mon - Friday 11,00am - 9pm<br>Saturday: 12,00am - 7pm<br>Sunday: Closed</p>

    <p class="social" style="top:402px"><span class="social__dot"></span>QuickChat</p>
    <p class="social" style="top:438px"><span class="social__dot"></span>SocialPage</p>
  </section>

</div>
</body>
</html>
```